BOLD & MINIMALIST DESIGN NEEDED

We want a very bold but minimalistic business card design that is impactful and utilizes both sides of the business card. Our current logo is included for your use.

We want bold fonts and good use of negative space. We don't want the logo to overpower the design.

Target Market(s)

Professionals who are building new commercial buildings.

Industry/Entity Type

Construction

Contact Information for Business Card

Name, Title, email, office phone, cell phone, website

Font styles to use
Serif
Sans Serif

Requirements
Must have
• Bold design!

```html
<!DOCTYPE html>
<html lang="en">
<head>
<meta charset="utf-8">
<title>Ridgeline Design + Build – Business Card</title>
<link rel="stylesheet" href="https://fonts.googleapis.com/css2?family=Montserrat:wght@400;500;700;800&display=swap">
<style>
  :root {
    --bg: #c9c9c9;
    --ink: #0c0c0d;
    --ink-soft: #1a1b1d;
    --paper: #ffffff;
    --accent: #76c92a;
    --text-light: #ffffff;
  }
  * { margin: 0; padding: 0; box-sizing: border-box; }
  html, body {
    width: 1200px; height: 800px; overflow: hidden;
    background: var(--bg);
    font-family: "Montserrat", sans-serif;
  }
  .card {
    position: absolute;
    left: 280px;
    width: 640px; height: 366px;
    overflow: hidden;
    box-shadow: 0 10px 24px rgba(0,0,0,0.25);
  }
  .card--front { top: 22px; background: var(--paper); border: 2px solid var(--accent); }
  .card--back { top: 412px; background: var(--ink); border: 2px solid var(--accent); }

  .front-shape { position: absolute; inset: 0; }

  .contact-block {
    position: absolute; left: 40px; top: 150px;
    color: var(--text-light);
  }
  .person-name { font-weight: 700; font-size: 25px; letter-spacing: 0.5px; text-transform: uppercase; }
  .person-title { font-weight: 500; font-size: 13px; color: var(--accent); text-transform: uppercase; letter-spacing: 0.5px; margin-top: 2px; }
  .contact-list { list-style: none; margin-top: 28px; }
  .contact-list li {
    display: flex; align-items: center; gap: 9px;
    font-size: 15px; font-weight: 400; line-height: 22px;
  }
  .contact-list svg { width: 13px; height: 13px; flex: none; }

  .wordmark { position: absolute; display: flex; flex-direction: column; }
  .wordmark-row { display: flex; align-items: center; gap: 10px; }
  .wordmark-square { background: var(--accent); flex: none; }
  .wordmark-name { font-weight: 800; text-transform: uppercase; line-height: 1; }
  .wordmark-tag { font-weight: 500; text-transform: uppercase; }

  .card--front .wordmark { left: 352px; top: 122px; }
  .card--front .wordmark-square { width: 22px; height: 22px; }
  .card--front .wordmark-name { font-size: 38px; color: var(--ink); }
  .card--front .wordmark-tag { font-size: 11px; letter-spacing: 7px; color: var(--ink); margin: 8px 0 0 34px; }

  .back-pattern {
    position: absolute; inset: 0;
    background: radial-gradient(ellipse at 70% 30%, #242528 0%, var(--ink-soft) 45%, var(--ink) 100%);
  }
  .card--back .wordmark { right: 40px; bottom: 46px; }
  .card--back .wordmark-square { width: 16px; height: 16px; }
  .card--back .wordmark-name { font-size: 26px; color: var(--text-light); }
  .card--back .wordmark-tag { font-size: 8px; letter-spacing: 5px; color: var(--text-light); margin: 6px 0 0 26px; }
</style>
</head>
<body>

<section class="card card--front">
  <svg class="front-shape" viewBox="0 0 636 362" preserveAspectRatio="none">
    <polygon points="0,0 216,0 380,362 0,362" fill="var(--ink)"/>
    <polyline points="8,8 210,8 372,354 8,354 8,8" fill="none" stroke="var(--accent)" stroke-width="1.5"/>
    <line x1="220" y1="0" x2="384" y2="362" stroke="var(--accent)" stroke-width="2"/>
  </svg>

  <div class="contact-block">
    <h1 class="person-name">Marcus Hale</h1>
    <p class="person-title">Managing Director</p>
    <ul class="contact-list">
      <li>
        <svg viewBox="0 0 16 16"><path d="M3 1l3 3-2 2c1 2 3 4 5 5l2-2 3 3-2 3C7 15 1 9 1 3z" fill="var(--accent)"/></svg>
        055-987 654 321
      </li>
      <li>
        <svg viewBox="0 0 16 16"><rect x="4" y="1" width="8" height="14" rx="1.5" fill="none" stroke="var(--accent)" stroke-width="1.8"/></svg>
        055-987 654 322
      </li>
      <li>
        <svg viewBox="0 0 16 16"><rect x="1" y="3" width="14" height="10" fill="var(--accent)"/><path d="M1 3l7 6 7-6" fill="none" stroke="var(--ink)" stroke-width="1.4"/></svg>
        hello@ridgelinebuild.com
      </li>
      <li>
        <svg viewBox="0 0 16 16"><circle cx="8" cy="8" r="7" fill="var(--accent)"/><path d="M1 8h14M8 1v14M3 4h10M3 12h10" stroke="var(--ink)" stroke-width="1"/></svg>
        www.ridgelinebuild.com
      </li>
    </ul>
  </div>

  <div class="wordmark">
    <div class="wordmark-row">
      <span class="wordmark-square"></span>
      <span class="wordmark-name">Ridgeline</span>
    </div>
    <span class="wordmark-tag">Design + Build</span>
  </div>
</section>

<section class="card card--back">
  <div class="back-pattern" role="img" aria-label="Tonal dark pattern of the company name repeated across the card"></div>
  <div class="wordmark">
    <div class="wordmark-row">
      <span class="wordmark-square"></span>
      <span class="wordmark-name">Ridgeline</span>
    </div>
    <span class="wordmark-tag">Design + Build</span>
  </div>
</section>

</body>
</html>
```